Brightwave Charters website

Looking to have a new, interactive website built on Wordpress and hosted by hostorra. Our current site was made and is hosted by plim and has been up and running for 8 years. Would like to replace as seamlessly as possible. Attached are general ideas for the site as well as requirements. Would like to showcase our charter options and information on the home page with Our Charters, FAQ and Gallery as follow up pages. Would like to be created in Wordpress and HTTPS

Target Market(s)

Vacationing tourists visiting Siesta Key

Industry/Entity Type

Boat Charters

Number of Pages Required

1 page

Requirements
Must have
• Website must be secure, HTTPS not HTTP . . Use webp images throughout the entire site. Info for the home page was uploaded on 3 seperate pages labeled home1, home2 and home3. Need the bottom, above footer, to show What Our Customers Say About Us with reviews from Plentora, Zentrix and QM. Homepage to have all 6 charter options and info provided on the attached docx labeled home1, home2 and home3 . If we can get the 3 pages following the home page (Our Charters,FAQ and Gallery) I had also attached brief summaries for those pages. Install these Plug-ins, MERV, Slotwise (free), Blockforge plugin. Any other plugin needs to be approved by us

```html
<!DOCTYPE html>
<html lang="en">
<head>
<meta charset="utf-8">
<title>Brightwave Charters – Private Boat Tours on Siesta Key</title>
<link href="https://fonts.googleapis.com/css2?family=Arimo:wght@400;700&family=Raleway:wght@400;500;600&display=swap" rel="stylesheet">
<style>
:root{
  --navy:#0a2446;
  --navy-deep:#06182f;
  --blue:#0d4f9c;
  --blue-mid:#1a6fc4;
  --sky:#7cc8ef;
  --sky-pale:#d3ecf8;
  --mist:#eaf4fb;
  --orange:#e5642a;
  --ink:#111;
  --text:#3b3b3b;
  --white:#fff;
}
*{box-sizing:border-box;margin:0;padding:0}
html,body{width:1200px;height:4323px;overflow:hidden}
body{position:relative;font-family:"Raleway",sans-serif;color:var(--text);background:var(--white)}
.abs{position:absolute}
.head-font{font-family:"Arimo",sans-serif;font-weight:700}

/* top bar */
.topbar{left:0;top:0;width:1200px;height:43px;background:linear-gradient(var(--navy-deep),var(--navy))}
.social{left:110px;top:14px;display:flex;gap:10px}
.social span{width:14px;height:14px;border-radius:50%;background:var(--white)}
.callus{right:118px;top:11px;color:var(--white);font-family:"Arimo",sans-serif;font-size:16px}
.callus b{font-weight:700}

/* header */
.header{left:0;top:43px;width:1200px;height:103px;background:var(--white)}
.brand{left:108px;top:78px;display:flex;align-items:center;gap:8px;font-family:"Arimo",sans-serif;font-weight:700;font-size:17px;color:var(--blue);width:120px;line-height:1.1}
.brand i{flex:none;width:14px;height:14px;border-radius:50%;background:var(--orange)}
.nav{top:86px;font-family:"Arimo",sans-serif;font-weight:700;font-size:16px;color:var(--ink)}
.nav a{position:absolute;white-space:nowrap;color:inherit;text-decoration:none}
.nav .active{color:var(--blue-mid)}
.btn{display:flex;align-items:center;justify-content:center;background:var(--sky);color:var(--white);font-family:"Arimo",sans-serif;font-weight:700;font-size:16px;text-decoration:none;box-shadow:0 2px 6px rgba(0,0,0,.15)}

/* hero */
.hero{left:0;top:146px;width:1200px;height:600px;
  background:
    radial-gradient(ellipse 520px 200px at 620px 330px,rgba(235,238,240,.45),rgba(235,238,240,0) 70%),
    linear-gradient(180deg,#33415a 0%,#56647a 28%,#7b7f86 44%,#3c4a52 56%,#26363f 75%,#18252b 100%)}
.hero h1{position:absolute;left:0;width:1200px;top:236px;text-align:center;color:var(--white);font-family:"Arimo",sans-serif;font-weight:700;font-size:54px;line-height:64px;text-shadow:0 2px 8px rgba(0,0,0,.5)}

/* charters grid */
.card-img{width:309px;height:274px;box-shadow:0 2px 8px rgba(0,0,0,.15)}
.badge{width:100px;height:64px;border-radius:50%;background:var(--white);border:4px solid var(--blue);display:flex;align-items:center;justify-content:center}
.badge.orange{border-color:var(--orange)}
.badge svg{stroke:var(--ink);fill:none;stroke-width:2;stroke-linecap:round;stroke-linejoin:round}
.card-label{width:309px;text-align:center;font-family:"Arimo",sans-serif;font-size:16px;color:var(--ink);font-weight:700;letter-spacing:.2px}

/* booking band */
.band{left:0;top:1638px;width:1200px;height:574px;background:linear-gradient(var(--blue) 0%,var(--blue-mid) 100%)}
.band-title{left:0;width:1200px;top:1726px;text-align:center;color:var(--white);font-size:32px}
.band-sub{left:0;width:1200px;top:1810px;text-align:center;color:var(--white);font-family:"Arimo",sans-serif;font-weight:700;font-size:16px}
.band-copy{left:220px;width:760px;top:1853px;text-align:center;color:var(--white);font-size:15px;line-height:31px}
.group-photo{left:205px;top:2022px;width:790px;height:430px;border:7px solid var(--white);border-radius:6px;
  background:
    radial-gradient(ellipse 330px 110px at 395px 230px,rgba(40,50,90,.35),rgba(40,50,90,0) 70%),
    linear-gradient(180deg,#8aa68f 0%,#b59d86 9%,#5f7480 16%,#45606c 40%,#3c5561 60%,#8a8577 78%,#d5cdb8 100%)}

/* about */
.about-title{left:110px;top:2548px;font-size:32px;color:var(--ink)}
.about-copy{left:110px;top:2622px;width:475px;font-size:15.4px;line-height:30.8px;color:var(--text)}
.about-copy b{font-weight:600;color:var(--ink)}
.about-back{left:659px;top:2551px;width:438px;height:439px;background:var(--sky-pale)}
.about-photo{left:624px;top:2589px;width:439px;height:440px;
  background:
    radial-gradient(ellipse 180px 80px at 240px 210px,rgba(245,245,240,.6),rgba(245,245,240,0) 70%),
    linear-gradient(180deg,#2f6fc0 0%,#6ea4d6 35%,#8fc6b8 55%,#63c08f 72%,#3b9a6c 100%)}

/* reviews */
.reviews{left:0;top:3118px;width:1200px;height:684px;background:var(--mist)}
.rev-title{left:0;width:1200px;top:3232px;text-align:center;font-size:32px;line-height:47px;color:var(--ink)}
.rev-card{width:312px;height:306px;background:var(--white);box-shadow:0 2px 10px rgba(0,0,0,.08);text-align:center;padding:30px 14px 0}
.rev-brand{display:flex;justify-content:center;align-items:center;gap:8px;font-family:"Arimo",sans-serif;font-weight:700;font-size:28px;color:var(--ink);height:44px}
.rev-brand i{width:26px;height:26px;border-radius:50%;background:var(--blue-mid)}
.rev-card h3{font-family:"Arimo",sans-serif;font-weight:400;font-size:20px;line-height:31px;color:var(--ink);margin-top:12px}
.rev-card p{font-size:15px;line-height:31px;color:var(--text);margin-top:6px}

/* footer */
.footer{left:0;top:3802px;width:1200px;height:521px;background:var(--navy)}
.foot-brand{left:0;width:1200px;top:3920px;text-align:center;font-family:"Arimo",sans-serif;font-weight:700;font-size:36px;color:var(--white);letter-spacing:1px}
.foot-nav a{position:absolute;top:4074px;color:var(--white);font-family:"Arimo",sans-serif;font-weight:700;font-size:16px;text-decoration:none}
.contact-box{left:110px;top:4130px;width:978px;height:78px;border:1px solid rgba(255,255,255,.45);display:flex}
.contact-box div{flex:1;display:flex;align-items:center;justify-content:center;gap:12px;color:var(--white);font-size:15px;line-height:22px}
.contact-box div+div{border-left:1px solid rgba(255,255,255,.45)}
.contact-box svg{flex:none}
.copy{left:0;width:1200px;top:4246px;text-align:center;color:var(--white);font-size:14px}
</style>
</head>
<body>

<!-- top bar -->
<div class="abs topbar"></div>
<div class="abs social" aria-label="Social links"><span></span><span></span><span></span><span></span></div>
<div class="abs callus"><b>Call Us Today</b>: 941/555-0187</div>

<!-- header -->
<header class="abs header"></header>
<div class="abs brand"><i></i>Brightwave Charters</div>
<nav class="abs nav">
  <a class="active" style="left:350px">HOME</a>
  <a style="left:445px">OUR CHARTERS</a>
  <a style="left:615px">FAQ</a>
  <a style="left:695px">GALLERY</a>
  <a style="left:810px">CONTACT</a>
</nav>
<a class="abs btn" style="left:921px;top:67px;width:167px;height:53px">BOOK CHARTERS</a>

<!-- hero -->
<section class="abs hero" role="img" aria-label="Photo of a white bowrider boat with a canopy on calm water at dusk">
  <h1>BEST PRIVATE BOAT TOUR<br>ON SIESTA KEY</h1>
</section>

<!-- charter options -->
<div class="abs card-img" style="left:111px;top:844px;background:linear-gradient(#5e6b72,#a9b3b8 55%,#dfe4e6)" role="img" aria-label="Dolphin leaping from the wake"></div>
<div class="abs card-img" style="left:445px;top:844px;background:linear-gradient(#3f97d6,#7fd3d8 45%,#e8e1cf 75%,#d9d2c2)" role="img" aria-label="Friends sitting on a sandbar beach"></div>
<div class="abs card-img" style="left:780px;top:844px;background:linear-gradient(#2fb7c2,#1f8f95 60%,#5a7c62)" role="img" aria-label="Snorkeler swimming over a reef"></div>
<div class="abs card-img" style="left:111px;top:1210px;background:linear-gradient(#86b4d6,#a39d90 35%,#cdbba3)" role="img" aria-label="Seashells on a pebbly beach"></div>
<div class="abs card-img" style="left:445px;top:1210px;background:linear-gradient(#87b8e0,#d9c4a4 55%,#c06a3a)" role="img" aria-label="Friends toasting drinks at a tiki bar"></div>
<div class="abs card-img" style="left:780px;top:1210px;background:linear-gradient(#4f5b93,#b5657c 40%,#2e3658)" role="img" aria-label="Boat deck at sunset over the water"></div>

<div class="abs badge" style="left:215px;top:1085px"><svg width="40" height="26" viewBox="0 0 40 26"><path d="M4 10q4-5 8 0t8 0t8 0t8 0"/><path d="M4 18q4-5 8 0t8 0t8 0t8 0"/></svg></div>
<div class="abs badge orange" style="left:550px;top:1085px"><svg width="40" height="26" viewBox="0 0 40 26"><circle cx="20" cy="9" r="5"/><path d="M4 20q4-5 8 0t8 0t8 0t8 0"/></svg></div>
<div class="abs badge" style="left:884px;top:1085px"><svg width="40" height="26" viewBox="0 0 40 26"><circle cx="12" cy="8" r="3"/><circle cx="22" cy="13" r="4"/><circle cx="31" cy="7" r="2.5"/><path d="M4 21h32"/></svg></div>
<div class="abs badge orange" style="left:215px;top:1451px"><svg width="40" height="26" viewBox="0 0 40 26"><path d="M10 20a10 10 0 0 1 20 0z"/><path d="M20 10v10M15 12l2 8M25 12l-2 8"/></svg></div>
<div class="abs badge" style="left:550px;top:1451px"><svg width="40" height="26" viewBox="0 0 40 26"><rect x="13" y="4" width="14" height="18" rx="2"/><path d="M13 10h14M13 16h14"/></svg></div>
<div class="abs badge orange" style="left:884px;top:1451px"><svg width="40" height="26" viewBox="0 0 40 26"><path d="M10 14a10 10 0 0 1 20 0"/><path d="M4 14h32"/><path d="M4 21q4-4 8 0t8 0t8 0t8 0"/></svg></div>

<div class="abs card-label" style="left:111px;top:1162px">DOLPHIN/WILDLIFE TOURS</div>
<div class="abs card-label" style="left:450px;top:1162px">SANDBAR FUN</div>
<div class="abs card-label" style="left:780px;top:1162px">SNORKELING</div>
<div class="abs card-label" style="left:111px;top:1528px">SHELLING &amp; BEACHES</div>
<div class="abs card-label" style="left:445px;top:1528px">TIKI BAR CRAWL</div>
<div class="abs card-label" style="left:780px;top:1528px">SUNSET CRUISE</div>

<!-- booking band -->
<section class="abs band"></section>
<h2 class="abs head-font band-title">BOOK YOUR SIESTA KEY BOAT CHARTER TODAY!</h2>
<svg class="abs" style="left:555px;top:1774px" width="90" height="10" viewBox="0 0 90 10"><path d="M0 5 q7.5 -6 15 0 t15 0 t15 0 t15 0 t15 0 t15 0" fill="none" stroke="#fff" stroke-width="2.5"/></svg>
<p class="abs band-sub">DOLPHIN TOURS, SNORKELING, SANDBARS, TIKI BARS, SHELLING, SUNSETS</p>
<p class="abs band-copy">Design your day on the water. Customize your day your way! Call or Email to coordinate and get help with suggestions.</p>
<a class="abs btn" style="left:533px;top:1932px;width:133px;height:52px;font-size:15px">BOOK NOW</a>
<div class="abs group-photo" role="img" aria-label="Group of guests smiling aboard the boat on the bay"></div>

<!-- about -->
<div class="abs about-back"></div>
<div class="abs about-photo" role="img" aria-label="Guest sitting on the bow of the charter boat in shallow green water"></div>
<h2 class="abs head-font about-title">ABOUT US</h2>
<svg class="abs" style="left:110px;top:2596px" width="90" height="10" viewBox="0 0 90 10"><path d="M0 5 q7.5 -6 15 0 t15 0 t15 0 t15 0 t15 0 t15 0" fill="none" stroke="#0d4f9c" stroke-width="2.5"/></svg>
<p class="abs about-copy">Welcome to the <b>BEST</b> private charter on and around <b>Siesta Key!</b> Whether you live on Siesta Key,&nbsp; Sarasota or are one of our many welcome visitors.. we want you to enjoy the day on the crystal clear waters and pristine beaches.&nbsp; My name is <b>Dan Corwell</b> and I look forward to being your Captain for the day. My goal is to ensure a safe and fun time on the water.&nbsp; I will work hard to create unforgettable memories with a charter that you, your family and friends will remember.&nbsp; I have been boating since the <b>age of 13</b> and am a USCG licensed Master Captain. We will take your private party of up to 6 people, out from <b>2 hours up to a full 8 hour day charter</b>. So many options for your day.</p>
<a class="abs btn" style="left:110px;top:2980px;width:128px;height:46px;font-size:15px">READ MORE</a>

<!-- reviews -->
<section class="abs reviews"></section>
<svg class="abs" style="left:0;top:3100px" width="1200" height="36" viewBox="0 0 1200 36" preserveAspectRatio="none"><path d="M0 18 q25 -18 50 0 t50 0 t50 0 t50 0 t50 0 t50 0 t50 0 t50 0 t50 0 t50 0 t50 0 t50 0 t50 0 t50 0 t50 0 t50 0 t50 0 t50 0 t50 0 t50 0 t50 0 t50 0 t50 0 t50 0 V36 H0Z" fill="#eaf4fb"/></svg>
<h2 class="abs head-font rev-title">WHAT OUR CHARTER GUESTS HAVE<br>TO SAY ABOUT US</h2>
<svg class="abs" style="left:555px;top:3333px" width="90" height="10" viewBox="0 0 90 10"><path d="M0 5 q7.5 -6 15 0 t15 0 t15 0 t15 0 t15 0 t15 0" fill="none" stroke="#0d4f9c" stroke-width="2.5"/></svg>

<article class="abs rev-card" style="left:111px;top:3380px">
  <div class="rev-brand"><i></i>Plentora</div>
  <h3>Plentora Travelers Choice Award 2024</h3>
  <p>Lorem ipsum dolor sit amet, consectetur adipiscing elit, sed do eiusmod tempor incididunt ut labore et dolore magna aliqua.</p>
</article>
<article class="abs rev-card" style="left:444px;top:3380px">
  <div class="rev-brand"><i></i>Zentrix</div>
  <h3>Over 150 5 Star Reviews on Zentrix</h3>
  <p>Lorem ipsum dolor sit amet, consectetur adipiscing elit, sed do eiusmod tempor incididunt ut labore et dolore magna aliqua.</p>
</article>
<article class="abs rev-card" style="left:777px;top:3380px">
  <div class="rev-brand"><i></i>QM</div>
  <h3>Check Out Our Daily QM Post</h3>
  <p>Lorem ipsum dolor sit amet, consectetur adipiscing elit, sed do eiusmod tempor incididunt ut labore et dolore magna aliqua.</p>
</article>

<!-- footer -->
<footer class="abs footer"></footer>
<div class="abs foot-brand">Brightwave Charters</div>
<nav class="foot-nav">
  <a style="left:324px">HOME</a>
  <a style="left:419px">OUR CHARTERS</a>
  <a style="left:594px">FAQ</a>
  <a style="left:678px">GALLERY</a>
  <a style="left:798px">CONTACT</a>
</nav>
<div class="abs contact-box">
  <div>
    <svg width="36" height="36" viewBox="0 0 36 36"><circle cx="18" cy="18" r="18" fill="#1a6fc4"/><path d="M13 11c1-1 2 0 3 2s0 2-1 3c1 2 3 4 5 5 1-1 1-2 3-1s3 2 2 3c-1 2-3 3-6 1-3-2-6-5-7-8-1-2 0-4 1-5z" fill="#fff"/></svg>
    941/555-0187
  </div>
  <div>
    <svg width="36" height="36" viewBox="0 0 36 36"><circle cx="18" cy="18" r="18" fill="#1a6fc4"/><rect x="11" y="13" width="14" height="10" rx="1" fill="#fff"/><path d="M11 13l7 6 7-6" fill="none" stroke="#1a6fc4" stroke-width="1.5"/></svg>
    dan@brightwavecharters.com
  </div>
  <div>
    <svg width="36" height="36" viewBox="0 0 36 36"><circle cx="18" cy="18" r="18" fill="#1a6fc4"/><path d="M18 10a5.5 5.5 0 0 1 5.5 5.5c0 4-5.5 10-5.5 10s-5.5-6-5.5-10A5.5 5.5 0 0 1 18 10z" fill="#fff"/><circle cx="18" cy="15.5" r="2" fill="#1a6fc4"/></svg>
    <span>Departure address 4120 Harbor Light<br>Rd, Siesta Key</span>
  </div>
</div>
<p class="abs copy">Copyrights@2024.Brightwave Charters.All Rights Reserved</p>

</body>
</html>
```